CREATE A KILLER WEBSITE DESIGN

We are a firearms training company that trains CIVILIANS (no police or military pictures - thank you!) to defend themselves and are looking for a killer design that's clean, easy to navigate and modern! We want the newest trends applied to this sight like a scrollable site so you can scroll down and see all the features. We are okay with tweaking the HTML but need the artistic design to look good. I'll provide a link to our current site along with a sight we really like so you can get an idea!

I'm supplying a PowerPoint Design we are going with from another designer so you can match the style to the new site.

PAGES: (Please use information from our current site. We like the information but just want a more polished look similar to the NWDPA site below but in our colors.)
Home - Long Form Scrolling Site. Top fold will be a video with a play button.
Harbor Institute - Seven Level Training Program Info Page That Will Contain A Video.
Contact Us - This will be a page that DOES NOT CONTAIN AN EMAIL ADDRESS. Just a contact us form
Meet The Trainer: Dennis Pollock

Our site:
https://www.brightmeadowskills.biz

Sights We Like:
https://www.nwdefenseplanners.com
https://quorvel.com
https://lindenplatecorp.com
https://www.velbrookgear.com

Target Market(s)

Men and women ages 21 to 100 years old

Industry/Entity Type

Self Defense

Number of Pages Required

5+ page

Font styles to use
Sans Serif

Colors
f26267

Requirements
Must have
• Clean and engaging. Use of colors that match our logo.
Should not have
• Poor design quality

```html
<!DOCTYPE html>
<html lang="en">
<head>
<meta charset="utf-8">
<title>Harbor Institute — Home Page Concepts</title>
<link rel="stylesheet" href="https://fonts.googleapis.com/css2?family=Orbitron:wght@500;600&family=Lato:wght@400;700&family=Montserrat:wght@500&display=swap">
<style>
:root{
  --coral:#f26267;
  --ink:#111111;
  --text:#333333;
  --white:#ffffff;
  --black:#000000;
  --panel:#151515;
  --board:#ececec;
  --field:#f2f2f2;
}
*{box-sizing:border-box;margin:0;padding:0}
html,body{width:731px;height:1200px;overflow:hidden;background:var(--board)}
body{font-family:'Lato',sans-serif;color:var(--text)}
.board{position:absolute;left:0;top:0;width:1500px;height:2464px;transform:scale(.48733);transform-origin:0 0}
.page{position:absolute;top:30px;width:690px;background:var(--white)}
.page--light{left:39px}
.page--dark{left:771px;background:var(--black);color:#ddd}
section,header,footer{position:relative;overflow:hidden}
.abs{position:absolute}
.display{font-family:'Orbitron',sans-serif;font-weight:500;letter-spacing:.5px;text-transform:uppercase}

/* top bar */
.topbar{height:32px;background:var(--coral);color:var(--white);font-size:8px;display:flex;align-items:center;padding:0 49px;gap:10px}
.topbar .dot{width:7px;height:7px;border-radius:50%;background:var(--white);display:inline-block}
.topbar .ico{width:18px;height:18px;border-radius:50%;background:var(--white);display:inline-flex;align-items:center;justify-content:center;margin-right:5px}
.topbar .item{display:flex;align-items:center;margin-left:12px}
.topbar .right{margin-left:auto;display:flex;align-items:center;gap:14px}

/* header */
.masthead{height:73px;display:flex;align-items:center;padding:0 30px}
.page--dark .masthead{background:var(--black)}
.brand{display:flex;align-items:center;gap:6px;width:94px}
.brand__mark{width:16px;height:16px;border-radius:50%;background:var(--coral);flex:none}
.brand__name{font-family:'Lato',sans-serif;font-weight:700;font-size:9px;line-height:1.1;color:var(--ink);text-transform:uppercase}
.page--dark .brand__name{color:var(--white)}
.nav{display:flex;gap:18px;font-family:'Montserrat',sans-serif;font-weight:500;font-size:9.5px;color:var(--ink);text-transform:uppercase}
.page--dark .nav{color:var(--white)}

/* hero */
.hero{height:322px;background:linear-gradient(100deg,#5a5454 0%,#7a6d6e 22%,#3e3a3b 45%,#2a2a2c 70%,#4a4a4c 100%)}
.hero__title{left:283px;top:93px;font-size:25px;line-height:27px;color:var(--white)}
.hero__lede{left:283px;top:157px;width:270px;font-size:8px;line-height:15px;color:var(--white)}
.btn{display:inline-flex;align-items:center;justify-content:center;height:24px;padding:0 9px;background:var(--coral);color:var(--white);font-family:'Orbitron',sans-serif;font-size:10px;text-transform:uppercase;letter-spacing:.3px}
.hero__cta{left:283px;top:202px;display:flex;gap:8px}
.hero__arrow{top:154px;width:10px;height:12px}
.hero__dots{left:333px;top:284px;display:flex;gap:5px;align-items:center}
.hero__dots i{width:3px;height:3px;border-radius:50%;background:var(--coral);display:block}
.hero__dots i:last-child{width:7px;height:7px}

/* about */
.about{height:318px}
.page--dark .about{height:313px;background:var(--black)}
.eyebrow{left:49px;top:63px;font-size:14px;color:var(--coral);text-transform:uppercase}
.about__name{left:49px;top:90px;font-size:21px;color:var(--ink)}
.page--dark .about__name{color:var(--white)}
.about__copy{left:49px;top:123px;width:272px;font-size:8px;line-height:14.8px;color:var(--text)}
.page--dark .about__copy{color:#e6e6e6}
.about__btn{left:49px;top:226px}
.portrait{left:417px;top:49px;width:224px;height:224px;border-radius:50%;background:radial-gradient(circle at 48% 42%,#d8d8d8 0%,#8e8e8e 45%,#3a3a3a 100%);border-right:3px solid var(--coral);border-bottom:2px solid var(--coral);box-shadow:0 4px 10px rgba(0,0,0,.18)}

/* video */
.video{height:350px;background:var(--coral)}
.section-title{width:100%;text-align:center;font-size:21px;line-height:30px}
.video .section-title{top:28px;color:var(--white)}
.video__frame{left:135px;top:78px;width:420px;height:239px;border:1px solid #fff;background:linear-gradient(120deg,#3a4a3c 0%,#556b5a 30%,#7a9aa0 55%,#3b3f52 80%,#2a2a33 100%)}

/* levels */
.levels{height:387px}
.page--dark .levels{height:377px;background:var(--panel)}
.levels .section-title{top:44px;color:var(--ink)}
.page--dark .levels .section-title{top:38px;color:var(--white)}
.steps{left:0;top:160px;width:690px;height:180px}
.page--dark .steps{top:155px}
.step{position:absolute;width:60px;height:60px;border-radius:50%;display:flex;align-items:center;justify-content:center;font-family:'Orbitron',sans-serif;font-size:34px;font-weight:500}
.step--up{border:2px solid var(--ink);color:var(--ink);top:0;background:var(--white)}
.page--dark .step--up{border-color:var(--white);color:var(--white);background:transparent}
.step--down{border:2px solid var(--coral);color:var(--coral);top:115px}
.step-label{position:absolute;width:90px;text-align:center;font-size:8px;line-height:14.5px;color:var(--text)}
.page--dark .step-label{color:#e6e6e6}
.connector{position:absolute;width:3px;display:flex;flex-direction:column;gap:5px}
.connector i{width:3px;height:3px;border-radius:50%;background:var(--coral);display:block}

/* testimonials */
.reviews{height:335px;background:var(--coral)}
.page--dark .reviews{height:321px;background:var(--black)}
.reviews .section-title{top:42px;color:var(--white)}
.card{position:absolute;top:115px;width:186px;height:170px;background:var(--white);padding:20px 14px 0 16px}
.page--dark .card{background:transparent;top:132px;padding:0;width:170px}
.card__quote{font-size:8px;line-height:14.8px;color:var(--text);height:76px}
.page--dark .card__quote{color:#e6e6e6}
.card__who{display:flex;align-items:center;gap:14px;margin-top:8px}
.avatar{width:50px;height:50px;border-radius:50%;background:linear-gradient(160deg,#c9c3bd,#6f6a66)}
.card__name{font-size:9px;color:var(--coral);line-height:18px}
.card__date{font-size:8.5px;color:var(--text)}
.page--dark .card__date{color:#e6e6e6}

/* contact */
.contact{height:380px}
.page--dark .contact{height:399px;background:var(--panel)}
.contact__title{left:49px;top:44px;font-size:21px;color:var(--ink)}
.page--dark .contact__title{top:55px;color:var(--white)}
.field{position:absolute;left:49px;width:246px;height:28px;border:1px solid #cfcfcf;background:var(--field);font-size:8px;color:#333;padding:9px 8px}
.page--dark .field{background:var(--black);border-color:#ccc;color:#eee}
.field--message{height:76px}
.contact__send{left:221px;width:74px;height:22px;padding:0}
.contact__photo{left:369px;top:88px;width:272px;height:206px;border-top:2px solid var(--coral);background:radial-gradient(circle at 52% 40%,#6a6e78 0%,#2c3240 45%,#12151c 100%)}

/* footer */
.footer{height:183px;background:var(--black);color:var(--white)}
.footer__item{position:absolute;left:49px;display:flex;align-items:flex-start;gap:8px;font-size:8px;line-height:14.5px}
.footer__ico{width:18px;height:18px;border-radius:50%;background:var(--coral);flex:none;display:flex;align-items:center;justify-content:center}
.footer__brand{left:297px;top:50px;width:120px;display:flex;flex-direction:column;align-items:center;gap:8px}
.footer__brand .brand__mark{width:30px;height:30px}
.footer__brand .brand__name{color:var(--white);font-size:13px;text-align:center}
.footer__about{left:503px;top:40px;width:140px;font-size:8px;line-height:14.8px}
.footer__about h4{font-size:9.5px;font-weight:700;margin-bottom:8px}
.socials{left:503px;top:122px;display:flex;gap:10px}
.socials i{width:22px;height:22px;border-radius:50%;background:var(--coral);display:block}
.copyright{height:24px;background:var(--coral);color:var(--white);font-size:8px;display:flex;align-items:center;justify-content:center}
</style>
</head>
<body>
<div class="board">

<!-- Light concept -->
<div class="page page--light">
  <div class="topbar">
    <span>Follow Us:</span><span class="dot"></span><span class="dot"></span><span class="dot"></span>
    <span class="item"><span class="ico"><svg width="9" height="9" viewBox="0 0 24 24"><path fill="#f26267" d="M6.6 10.8a15 15 0 0 0 6.6 6.6l2.2-2.2a1 1 0 0 1 1-.25 11.4 11.4 0 0 0 3.6.6 1 1 0 0 1 1 1V20a1 1 0 0 1-1 1A17 17 0 0 1 3 4a1 1 0 0 1 1-1h3.5a1 1 0 0 1 1 1c0 1.25.2 2.45.6 3.6a1 1 0 0 1-.25 1z"/></svg></span>555-014-2277</span>
    <span class="item"><span class="ico"><svg width="9" height="9" viewBox="0 0 24 24"><path fill="#f26267" d="M3 5h18v14H3zm2 2v.5l7 4.5 7-4.5V7z"/></svg></span>frontdesk@harborinstitute.net</span>
    <span class="right"><span class="item"><span class="ico"></span>Login</span>
    <svg width="14" height="12" viewBox="0 0 24 20"><path fill="none" stroke="#fff" stroke-width="2" d="M1 2h4l3 11h12l2-8H7"/><circle cx="9" cy="17" r="1.6" fill="#fff"/><circle cx="18" cy="17" r="1.6" fill="#fff"/></svg></span>
  </div>
  <header class="masthead">
    <div class="brand"><span class="brand__mark"></span><span class="brand__name">Harbor<br>Institute</span></div>
    <nav class="nav"><span>Home</span><span>About Us</span><span>Testimonials</span><span>Upcoming Classes</span><span>Shop</span><span>Videos</span><span>Contact Us</span></nav>
  </header>
  <section class="hero" role="img" aria-label="Photo of a woman with ear and eye protection aiming a pistol at an indoor range">
    <svg class="abs hero__arrow" style="left:21px" viewBox="0 0 10 12"><path d="M7 1 2 6l5 5" fill="none" stroke="#fff" stroke-width="2"/></svg>
    <svg class="abs hero__arrow" style="left:662px" viewBox="0 0 10 12"><path d="M3 1l5 5-5 5" fill="none" stroke="#fff" stroke-width="2"/></svg>
    <h1 class="abs display hero__title">Harbor Institute<br>Prepared to Prevail</h1>
    <p class="abs hero__lede">Dennis Pollock is a 3rd generation Cedar Cove native and delighted to be a part of this great community.</p>
    <div class="abs hero__cta"><span class="btn">Get Started</span><span class="btn" style="padding:0 12px 0 14px">Video&nbsp;&nbsp;&nbsp;&nbsp;<svg width="11" height="11" viewBox="0 0 12 12"><circle cx="6" cy="6" r="5" fill="none" stroke="#fff"/><path d="M5 4l3 2-3 2z" fill="#fff"/></svg></span></div>
    <div class="abs hero__dots"><i></i><i></i><i></i></div>
  </section>
  <section class="about">
    <p class="abs eyebrow">About the Instructor</p>
    <h2 class="abs display about__name">Dennis Pollock</h2>
    <p class="abs about__copy">Dennis Pollock is a 3rd generation Cedar Cove native and delighted to be a part of this great community. He is a true security expert with 25 years of experience in the security industry. He has appeared on Channel 4, 7, 9 &amp; 12 news outlets. He has been Featured in numerous publications and has trained thousands to protect themselves and their homes from thugs and thieves.</p>
    <span class="abs btn about__btn">Get Started</span>
    <div class="abs portrait" role="img" aria-label="Black and white portrait of the instructor"></div>
  </section>
  <section class="video">
    <h2 class="abs display section-title">Our Video</h2>
    <div class="abs video__frame" role="img" aria-label="Video still of a student firing at a virtual target screen"></div>
  </section>
  <section class="levels">
    <h2 class="abs display section-title">Our 7 Levels of Training<br>Take You From Zero to Hero</h2>
    <div class="abs steps">
      <div class="step-label" style="left:36px;top:50px">Concealed Carry<br>Class</div>
      <div class="connector" style="left:80px;top:87px"><i></i><i></i><i></i></div>
      <div class="step step--down" style="left:51px">1</div>
      <div class="step step--up" style="left:141px">2</div>
      <div class="connector" style="left:170px;top:70px"><i></i><i></i><i></i></div>
      <div class="step-label" style="left:126px;top:97px">Dynamic Defensive<br>Shooting</div>
      <div class="step-label" style="left:217px;top:50px">Fine Tuning Your<br>Technique</div>
      <div class="connector" style="left:261px;top:87px"><i></i><i></i><i></i></div>
      <div class="step step--down" style="left:232px">3</div>
      <div class="step step--up" style="left:318px">4</div>
      <div class="connector" style="left:347px;top:70px"><i></i><i></i><i></i></div>
      <div class="step-label" style="left:303px;top:97px">Virtual Threat lab</div>
      <div class="step-label" style="left:389px;top:50px">Tactical Skill<br>&amp; Drills</div>
      <div class="connector" style="left:433px;top:87px"><i></i><i></i><i></i></div>
      <div class="step step--down" style="left:404px">5</div>
      <div class="step step--up" style="left:493px">6</div>
      <div class="connector" style="left:522px;top:70px"><i></i><i></i><i></i></div>
      <div class="step-label" style="left:478px;top:97px">Close Quarters<br>Defense</div>
      <div class="step-label" style="left:566px;top:50px">Live Scenario<br>Threat Lab</div>
      <div class="connector" style="left:610px;top:87px"><i></i><i></i><i></i></div>
      <div class="step step--down" style="left:581px">7</div>
    </div>
  </section>
  <section class="reviews">
    <h2 class="abs display section-title">Out Testimonials</h2>
    <div class="card" style="left:48px"><p class="card__quote">"I had never held a gun when I took the Harbor Institute class and I'm hooked! I'm going all the way to level 7! Thank you Harbor Institute!</p><div class="card__who"><div class="avatar" role="img" aria-label="Student portrait"></div><div><p class="card__name">Renee K.</p><p class="card__date">October 14, 2017</p></div></div></div>
    <div class="card" style="left:250px"><p class="card__quote">"I was mugged here in Cedar Cove and lived in fear ever since. It stole my happiness and I became scared to go out. I'm a Level 4 student and I feel sorry for the next thug that tries me!"</p><div class="card__who"><div class="avatar" role="img" aria-label="Student portrait"></div><div><p class="card__name">Maya L.</p><p class="card__date">December 9, 2017</p></div></div></div>
    <div class="card" style="left:452px"><p class="card__quote">"I've been shooting for years and already had my concealed weapons license. My first class was a gun shop class and a waste of money. Dennis took the time to show me how to properly grip my gun.</p><div class="card__who"><div class="avatar" role="img" aria-label="Student portrait"></div><div><p class="card__name">Frank D.</p><p class="card__date">March 3 2018</p></div></div></div>
  </section>
  <section class="contact">
    <h2 class="abs display contact__title">Get in Touch</h2>
    <div class="field" style="top:91px">Name:</div>
    <div class="field" style="top:133px">Email:</div>
    <div class="field" style="top:175px">Address:</div>
    <div class="field field--message" style="top:217px">Message:</div>
    <span class="abs btn contact__send" style="top:308px">Send</span>
    <div class="abs contact__photo" role="img" aria-label="Photo of a hooded figure pointing a handgun toward the viewer, face blurred"></div>
  </section>
  <footer class="footer">
    <div class="footer__item" style="top:42px"><span class="footer__ico"></span><span style="padding-top:2px">555-014-2277</span></div>
    <div class="footer__item" style="top:79px"><span class="footer__ico"></span><span style="padding-top:2px">frontdesk@harborinstitute.net</span></div>
    <div class="footer__item" style="top:111px"><span class="footer__ico"></span><span>P.O. Box 4410<br>Cedar Cove, FL 32190</span></div>
    <div class="abs footer__brand"><span class="brand__mark"></span><span class="brand__name">Harbor Institute</span></div>
    <div class="abs footer__about"><h4>About</h4><p>Dennis Pollock is a 3rd generation Cedar Cove native and delighted to be a part of this great community.</p></div>
    <div class="abs socials"><i></i><i></i><i></i><i></i></div>
  </footer>
  <div class="copyright">Copyright Harbor Institute 2020 - All Rights Reserved</div>
</div>

<!-- Dark concept -->
<div class="page page--dark">
  <div class="topbar">
    <span>Follow Us:</span><span class="dot"></span><span class="dot"></span><span class="dot"></span>
    <span class="item"><span class="ico"><svg width="9" height="9" viewBox="0 0 24 24"><path fill="#f26267" d="M6.6 10.8a15 15 0 0 0 6.6 6.6l2.2-2.2a1 1 0 0 1 1-.25 11.4 11.4 0 0 0 3.6.6 1 1 0 0 1 1 1V20a1 1 0 0 1-1 1A17 17 0 0 1 3 4a1 1 0 0 1 1-1h3.5a1 1 0 0 1 1 1c0 1.25.2 2.45.6 3.6a1 1 0 0 1-.25 1z"/></svg></span>555-014-2277</span>
    <span class="item"><span class="ico"><svg width="9" height="9" viewBox="0 0 24 24"><path fill="#f26267" d="M3 5h18v14H3zm2 2v.5l7 4.5 7-4.5V7z"/></svg></span>frontdesk@harborinstitute.net</span>
    <span class="right"><span class="item"><span class="ico"></span>Login</span>
    <svg width="14" height="12" viewBox="0 0 24 20"><path fill="none" stroke="#fff" stroke-width="2" d="M1 2h4l3 11h12l2-8H7"/><circle cx="9" cy="17" r="1.6" fill="#fff"/><circle cx="18" cy="17" r="1.6" fill="#fff"/></svg></span>
  </div>
  <header class="masthead">
    <div class="brand"><span class="brand__mark"></span><span class="brand__name">Harbor<br>Institute</span></div>
    <nav class="nav"><span>Home</span><span>About Us</span><span>Testimonials</span><span>Upcoming Classes</span><span>Shop</span><span>Videos</span><span>Contact Us</span></nav>
  </header>
  <section class="hero" role="img" aria-label="Photo of a woman with ear and eye protection aiming a pistol at an indoor range">
    <svg class="abs hero__arrow" style="left:21px" viewBox="0 0 10 12"><path d="M7 1 2 6l5 5" fill="none" stroke="#fff" stroke-width="2"/></svg>
    <svg class="abs hero__arrow" style="left:662px" viewBox="0 0 10 12"><path d="M3 1l5 5-5 5" fill="none" stroke="#fff" stroke-width="2"/></svg>
    <h1 class="abs display hero__title">Harbor Institute<br>Prepared to Prevail</h1>
    <p class="abs hero__lede">Dennis Pollock is a 3rd generation Cedar Cove native and delighted to be a part of this great community.</p>
    <div class="abs hero__cta"><span class="btn">Get Started</span><span class="btn" style="padding:0 12px 0 14px">Video&nbsp;&nbsp;&nbsp;&nbsp;<svg width="11" height="11" viewBox="0 0 12 12"><circle cx="6" cy="6" r="5" fill="none" stroke="#fff"/><path d="M5 4l3 2-3 2z" fill="#fff"/></svg></span></div>
    <div class="abs hero__dots"><i></i><i></i><i></i></div>
  </section>
  <section class="about">
    <p class="abs eyebrow">About the Instructor</p>
    <h2 class="abs display about__name">Dennis Pollock</h2>
    <p class="abs about__copy">Dennis Pollock is a 3rd generation Cedar Cove native and delighted to be a part of this great community. He is a true security expert with 25 years of experience in the security industry. He has appeared on Channel 4, 7, 9 &amp; 12 news outlets. He has been Featured in numerous publications and has trained thousands to protect themselves and their homes from thugs and thieves.</p>
    <span class="abs btn about__btn">Get Started</span>
    <div class="abs portrait" role="img" aria-label="Black and white portrait of the instructor"></div>
  </section>
  <section class="levels">
    <h2 class="abs display section-title">Our 7 Levels of Training<br>Take You From Zero to Hero</h2>
    <div class="abs steps">
      <div class="step-label" style="left:36px;top:50px">Concealed Carry<br>Class</div>
      <div class="connector" style="left:80px;top:87px"><i></i><i></i><i></i></div>
      <div class="step step--down" style="left:51px">1</div>
      <div class="step step--up" style="left:141px">2</div>
      <div class="connector" style="left:170px;top:70px"><i></i><i></i><i></i></div>
      <div class="step-label" style="left:126px;top:97px">Dynamic Defensive<br>Shooting</div>
      <div class="step-label" style="left:217px;top:50px">Fine Tuning Your<br>Technique</div>
      <div class="connector" style="left:261px;top:87px"><i></i><i></i><i></i></div>
      <div class="step step--down" style="left:232px">3</div>
      <div class="step step--up" style="left:318px">4</div>
      <div class="connector" style="left:347px;top:70px"><i></i><i></i><i></i></div>
      <div class="step-label" style="left:303px;top:97px">Virtual Threat lab</div>
      <div class="step-label" style="left:389px;top:50px">Tactical Skill<br>&amp; Drills</div>
      <div class="connector" style="left:433px;top:87px"><i></i><i></i><i></i></div>
      <div class="step step--down" style="left:404px">5</div>
      <div class="step step--up" style="left:493px">6</div>
      <div class="connector" style="left:522px;top:70px"><i></i><i></i><i></i></div>
      <div class="step-label" style="left:478px;top:97px">Close Quarters<br>Defense</div>
      <div class="step-label" style="left:566px;top:50px">Live Scenario<br>Threat Lab</div>
      <div class="connector" style="left:610px;top:87px"><i></i><i></i><i></i></div>
      <div class="step step--down" style="left:581px">7</div>
    </div>
  </section>
  <section class="reviews">
    <h2 class="abs display section-title">Out Testimonials</h2>
    <div class="card" style="left:64px"><p class="card__quote">"I had never held a gun when I took the Harbor Institute class and I'm hooked! I'm going all the way to level 7! Thank you Harbor Institute!</p><div class="card__who"><div class="avatar" role="img" aria-label="Student portrait"></div><div><p class="card__name">Renee K.</p><p class="card__date">October 14, 2017</p></div></div></div>
    <div class="card" style="left:259px"><p class="card__quote">"I was mugged here in Cedar Cove and lived in fear ever since. It stole my happiness and I became scared to go out. I'm a Level 4 student and I feel sorry for the next thug that tries me!"</p><div class="card__who"><div class="avatar" role="img" aria-label="Student portrait"></div><div><p class="card__name">Maya L.</p><p class="card__date">December 9, 2017</p></div></div></div>
    <div class="card" style="left:462px"><p class="card__quote">"I've been shooting for years and already had my concealed weapons license. My first class was a gun shop class and a waste of money. Dennis took the time to show me how to properly grip my gun.</p><div class="card__who"><div class="avatar" role="img" aria-label="Student portrait"></div><div><p class="card__name">Frank D.</p><p class="card__date">March 3 2018</p></div></div></div>
  </section>
  <section class="contact">
    <h2 class="abs display contact__title">Get in Touch</h2>
    <div class="field" style="top:101px">Name:</div>
    <div class="field" style="top:143px">Email:</div>
    <div class="field" style="top:185px">Address:</div>
    <div class="field field--message" style="top:228px">Message:</div>
    <span class="abs btn contact__send" style="top:319px">Send</span>
    <div class="abs contact__photo" style="left:369px;top:98px;height:207px;border-top:0" role="img" aria-label="Photo of a hooded figure pointing a handgun toward the viewer, face blurred"></div>
  </section>
  <footer class="footer">
    <div class="footer__item" style="top:42px"><span class="footer__ico"></span><span style="padding-top:2px">555-014-2277</span></div>
    <div class="footer__item" style="top:79px"><span class="footer__ico"></span><span style="padding-top:2px">frontdesk@harborinstitute.net</span></div>
    <div class="footer__item" style="top:111px"><span class="footer__ico"></span><span>P.O. Box 4410<br>Cedar Cove, FL 32190</span></div>
    <div class="abs footer__brand"><span class="brand__mark"></span><span class="brand__name">Harbor Institute</span></div>
    <div class="abs footer__about"><h4>About</h4><p>Dennis Pollock is a 3rd generation Cedar Cove native and delighted to be a part of this great community.</p></div>
    <div class="abs socials"><i></i><i></i><i></i><i></i></div>
  </footer>
  <div class="copyright">Copyright Harbor Institute 2020 - All Rights Reserved</div>
</div>

</div>
</body>
</html>
```